Complete Website Redesign

We need a complete revamp of our website. Need to add interactive custmer catalog seection tools. Need to add customer spec input for recommended product search results. Need a cutomer lead and opportunity contact capability. Need a complete Branding message revamp. Primary visuals will be prodcut pictures and case studies.
Target Market(s)
Industrial Customers in the high durability Air movement and fan/blower space; high durability enclosure and flow industries ie. mining, chamicals, manufacturing, water treatment, chemical in use manufacturing
Look and feel
Each slider illustrates characteristics of the customer's brand and the style your logo design should communicate.

```html
<!DOCTYPE html>
<html lang="en">
<head>
<meta charset="utf-8">
<title>Quarnell Composites – About Us</title>
<link href="https://fonts.googleapis.com/css2?family=Open+Sans:wght@400;600;700&family=Cabin:wght@400;500;600&display=swap" rel="stylesheet">
<style>
:root{
  --page-bg:#2a2a2c;
  --topbar:#3f7fc4;
  --accent-yellow:#f5e52a;
  --navy:#1c2a83;
  --red:#b2000e;
  --dark:#2c2a30;
  --blue-btn:#0a6cc4;
  --avatar:#c5cde0;
  --text:#333;
  --white:#fff;
}
*{margin:0;padding:0;box-sizing:border-box}
html,body{width:1200px;height:1000px;overflow:hidden}
body{background:var(--page-bg);font-family:"Open Sans",sans-serif;position:relative}
.site{position:absolute;left:63px;top:0;width:1081px;height:968px;background:#fdfcfd}
.topbar{position:absolute;left:0;top:0;width:100%;height:41px;background:var(--topbar);border-bottom:2px solid #3570b0}
.topbar .call{position:absolute;left:62px;top:9px;color:var(--white);font-size:20px;font-weight:600;letter-spacing:.5px}
.topbar .call b{color:var(--accent-yellow);font-weight:600}
.topbar .account{position:absolute;right:76px;top:11px;color:var(--white);font-size:16px;font-weight:600;letter-spacing:.5px;word-spacing:14px}
.header{position:absolute;left:0;top:41px;width:100%;height:90px;background:linear-gradient(#fff 0%,#f1f1f1 70%,#dedede 100%);box-shadow:0 2px 4px rgba(0,0,0,.15)}
.brand{position:absolute;left:74px;top:36px;display:flex;align-items:center;gap:8px;color:var(--navy);font-size:15px;font-weight:600;white-space:nowrap}
.brand .mark{width:16px;height:16px;background:var(--navy)}
.nav{position:absolute;top:37px;left:0;width:100%;font-size:15px;color:#222}
.nav span{position:absolute;top:0;white-space:nowrap}
.nav .active{background:var(--dark);color:var(--white);border-radius:7px;padding:3px 12px;top:-3px}
.nav .caret{position:absolute;left:455px;top:23px;width:0;height:0;border-left:5px solid transparent;border-right:5px solid transparent;border-top:7px solid var(--red)}
.hero{position:absolute;left:64px;top:145px;width:939px;height:175px}
.hero .band{height:94px;background:linear-gradient(#3f7fc4,#2d64a8);text-align:center;color:var(--white);font-family:"Cabin",sans-serif;font-size:21px;line-height:25px;padding-top:17px}
.hero .search{height:81px;background:var(--dark);position:relative}
.hero label{position:absolute;left:89px;top:25px;color:var(--white);font-size:18px}
.hero .field{position:absolute;left:312px;top:19px;width:424px;height:30px;background:#17151a;border:1px solid #777}
.hero .submit{position:absolute;left:754px;top:19px;width:95px;height:29px;border-radius:5px;background:#7f9993;color:var(--white);font-size:15px;text-align:center;line-height:28px}
.hero .hint{position:absolute;left:0;width:100%;top:59px;text-align:center;color:#f5c400;font-size:11px;font-weight:600}
.about-tab{position:absolute;left:64px;top:338px;width:182px;height:34px;background:var(--red);clip-path:polygon(0 0,155px 0,100% 100%,0 100%);color:var(--white);font-size:18px;font-weight:600;padding:5px 0 0 17px;letter-spacing:.5px}
.about-fold{position:absolute;left:64px;top:329px;width:0;height:0;border-left:9px solid transparent;border-bottom:9px solid #7a0009}
.about-text{position:absolute;left:74px;top:375px;width:930px;border-left:1px solid #ccc;padding:8px 40px 6px 21px;font-size:12.5px;line-height:16px;color:var(--text)}
.section-title{position:absolute;left:76px;top:440px;width:922px;padding-left:30px;text-align:center;color:var(--red);font-size:21px;font-weight:400}
.section-title::before,.section-title::after{content:"";position:absolute;top:14px;height:1px}
.section-title::before{left:0;width:381px;background:linear-gradient(90deg,transparent,#555)}
.section-title::after{right:0;width:357px;background:linear-gradient(90deg,#222,transparent)}
.person{position:absolute;top:518px;width:220px;text-align:center;font-family:"Cabin",sans-serif}
.person .name{font-size:16px;color:#222;white-space:nowrap}
.person .role{font-size:16px;color:var(--red);font-weight:500;margin-top:6px;white-space:nowrap}
.person .avatar{display:block;width:153px;height:153px;border-radius:50%;background:var(--avatar);margin:8px auto 0}
.person .more{position:relative;display:block;width:108px;height:28px;margin:3px auto 0;background:var(--blue-btn);border-radius:5px;color:var(--white);font-family:"Open Sans",sans-serif;font-size:13px;font-weight:600;line-height:28px}
.person .more::after{content:"";position:absolute;right:10px;top:-7px;border-left:7px solid transparent;border-right:7px solid transparent;border-bottom:8px solid var(--blue-btn)}
.footer{position:absolute;left:0;top:828px;width:100%;height:140px;background:var(--dark)}
.footer h4{position:absolute;top:9px;color:var(--white);font-size:13.5px;font-weight:600;text-align:center}
.quote{position:absolute;left:21px;top:32px;width:196px;height:80px;background:#1a181c;border-radius:10px;color:var(--white);font-size:9.5px;font-weight:600;line-height:12.5px;padding:9px 10px}
.quote em{font-style:normal;color:#e8202c}
.quote-tail{position:absolute;left:106px;top:110px;width:0;height:0;border-left:30px solid transparent;border-top:22px solid #1a181c}
.quote-by{position:absolute;left:157px;top:122px;color:#ddd;font-size:10.5px}
.social{position:absolute;width:31px;height:31px;border-radius:6px}
.panel{position:absolute;top:32px;height:108px;background:#1c1a1e;border-radius:10px 10px 0 0}
.input{position:absolute;background:#3a383e;color:#aaa;font-size:11px;padding:3px 8px}
.btn{position:absolute;height:17px;color:var(--white);font-size:11.5px;font-weight:600;text-align:center;line-height:17px}
.copyright{position:absolute;left:0;top:975px;width:1200px;text-align:center;color:#bbb;font-size:13px}
</style>
</head>
<body>
<div class="site">
  <div class="topbar">
    <div class="call"><b>CALL US</b> : +1 (800) 555 0142</div>
    <div class="account">LOGIN | SIGNUP</div>
  </div>
  <div class="header">
    <div class="brand"><span class="mark"></span>Quarnell Composites, LLC</div>
    <nav class="nav">
      <span style="left:340px">HOME</span>
      <span style="left:423px">PRODUCTS</span><i class="caret"></i>
      <span class="active" style="left:520px">ABOUT US</span>
      <span style="left:640px">MISSION</span>
      <span style="left:732px">REQUEST INFORMATION</span>
      <span style="left:928px">CONTACTS</span>
    </nav>
  </div>

  <section class="hero">
    <div class="band">We have a wide selecion of fiberglass fans and other corrosion resistant air handling<br>solutions for OEMs, Contractors and Plant Maintenance Operations.</div>
    <div class="search">
      <label>PRODUCT SELECTION</label>
      <div class="field"></div>
      <div class="submit">Submit</div>
      <div class="hint">To verify a catalog numberand access product information, enter the complete number (including dashes) above.</div>
    </div>
  </section>

  <div class="about-fold"></div>
  <div class="about-tab">ABOUT US</div>
  <p class="about-text">Here at Quarnell Composites, LLC., we are focused on continuous improvement of our operation. Our objective and vision is to capture more market share geographically while serving the petrochemical, military, industrial and construction markets and grow our presence in the energy industry.</p>

  <h3 class="section-title">OUR PERSONNEL</h3>

  <div class="person" style="left:29px"><div class="name">DANIEL HARWICK</div><div class="role">PRESIDENT</div><span class="avatar" role="img" aria-label="Portrait placeholder for Daniel Harwick"></span><span class="more">More &gt;&gt;</span></div>
  <div class="person" style="left:225px"><div class="name">TOM BELCARO</div><div class="role">VICE PRESIDENT</div><span class="avatar" role="img" aria-label="Portrait placeholder for Tom Belcaro"></span><span class="more">More &gt;&gt;</span></div>
  <div class="person" style="left:415px"><div class="name">NINA OSTROW</div><div class="role">ADMINISTRATIVE ASSISTANT</div><span class="avatar" role="img" aria-label="Portrait placeholder for Nina Ostrow"></span><span class="more">More &gt;&gt;</span></div>
  <div class="person" style="left:616px"><div class="name">PAUL VENNER</div><div class="role">INDUSTRIAL ENGINEER</div><span class="avatar" role="img" aria-label="Portrait placeholder for Paul Venner"></span><span class="more">More &gt;&gt;</span></div>
  <div class="person" style="left:817px"><div class="name">EVAN LINDQVIST</div><div class="role">ASSOCIATE ENGINEER</div><span class="avatar" role="img" aria-label="Portrait placeholder for Evan Lindqvist"></span><span class="more">More &gt;&gt;</span></div>

  <footer class="footer">
    <h4 style="left:21px;width:180px">TESTIMONIALS</h4>
    <div class="quote">I have been very satisfied with all of the service provided by <em>Quarnell</em>. All of your personnel are really focused and were so courteous and professional acting.</div>
    <div class="quote-tail"></div>
    <div class="quote-by">Mr. Reed</div>

    <h4 style="left:300px;width:120px">FOLLOW US</h4>
    <span class="social" style="left:289px;top:38px;background:#2a9fe0"></span>
    <span class="social" style="left:326px;top:38px;background:#d83a2e"></span>
    <span class="social" style="left:364px;top:38px;background:#3a5a9c"></span>
    <span class="social" style="left:401px;top:38px;background:#1d6fb0"></span>
    <span class="social" style="left:289px;top:80px;background:#c8202a"></span>
    <span class="social" style="left:326px;top:80px;background:#3aa83a"></span>
    <span class="social" style="left:364px;top:80px;background:#f07a1e"></span>

    <h4 style="left:570px;width:110px">NEWSLETTER</h4>
    <div class="panel" style="left:511px;width:236px">
      <div class="input" style="left:23px;top:12px;width:194px;height:21px">Your Name</div>
      <div class="input" style="left:23px;top:40px;width:194px;height:21px">Your Email</div>
      <div class="btn" style="left:163px;top:85px;width:53px;background:var(--red)">Submit</div>
    </div>

    <h4 style="left:860px;width:126px">QUICK CONTACT</h4>
    <div class="panel" style="left:805px;width:236px">
      <div class="input" style="left:18px;top:12px;width:194px;height:21px">Your Email</div>
      <div class="input" style="left:18px;top:40px;width:194px;height:40px">Your Message</div>
      <div class="btn" style="left:98px;top:85px;width:54px;background:#3e77b8">Reset</div>
      <div class="btn" style="left:159px;top:85px;width:53px;background:var(--red)">Submit</div>
    </div>
  </footer>
</div>
<div class="copyright">Copyright ©&nbsp; Quarnell&nbsp; 2013. All rights reserved.</div>
</body>
</html>
```